Every Shelf Set Neatly or ESN Organized needs a business card design. ESN Organized is a professi

We need a business card design that is clean, sharp and conveys a sense of organization. I already have a logo.

Target Market(s)

Families (specifically mothers), small business owners, parents, seniors

Industry/Entity Type

Business

Contact Information for Business Card

My website is www.esnorganized-example.com and my Facebook page is http://www.sociallink-example.com/everyshelfsetneatly. The phone number is 418-552-7094 and I want to be listed as Lorna M. Pelham, Owner

Requirements
Must have
• My logo.

```html
<!DOCTYPE html>
<html lang="en">
<head>
<meta charset="utf-8">
<title>Every Shelf Set Neatly – Business Card</title>
<link rel="stylesheet" href="https://fonts.googleapis.com/css2?family=Karla:wght@400&family=Lora:wght@400&family=Montserrat:wght@400&display=swap">
<style>
  :root {
    --backdrop: #ece9e4;
    --card: #ffffff;
    --ink: #1c1c1c;
    --brand-blue: #1b7bbf;
    --shadow: rgba(0, 0, 0, 0.12);
  }
  * { margin: 0; padding: 0; box-sizing: border-box; }
  html, body {
    width: 1200px;
    height: 1200px;
    overflow: hidden;
    background: var(--backdrop);
  }
  .canvas {
    position: relative;
    width: 1200px;
    height: 1200px;
  }
  .business-card {
    position: absolute;
    left: 100px;
    top: 314px;
    width: 1000px;
    height: 572px;
    background: var(--card);
    box-shadow: 0 6px 24px var(--shadow);
  }
  .brand-lockup {
    position: absolute;
    left: 78px;
    top: 110px;
    display: flex;
    align-items: center;
    gap: 18px;
  }
  .brand-mark {
    width: 34px;
    height: 34px;
    background: var(--brand-blue);
  }
  .brand-name {
    font-family: "Montserrat", sans-serif;
    font-weight: 400;
    font-size: 44px;
    letter-spacing: 0.12em;
    color: var(--ink);
    white-space: nowrap;
  }
  .contact-block {
    position: absolute;
    left: 520px;
    top: 222px;
  }
  .person-name {
    font-family: "Lora", serif;
    font-size: 34px;
    color: var(--brand-blue);
    line-height: 1.1;
  }
  .person-title {
    font-family: "Karla", sans-serif;
    font-size: 22px;
    color: var(--ink);
    margin-top: 8px;
  }
  .contact-list {
    list-style: none;
    margin-top: 44px;
  }
  .contact-item {
    display: flex;
    align-items: center;
    gap: 10px;
    font-family: "Karla", sans-serif;
    font-size: 25px;
    color: var(--ink);
    margin-bottom: 14px;
    white-space: nowrap;
  }
  .contact-icon {
    width: 20px;
    height: 20px;
    flex: none;
  }
  .social-line {
    position: absolute;
    left: 78px;
    bottom: 62px;
    display: flex;
    align-items: center;
    gap: 10px;
    font-family: "Karla", sans-serif;
    font-size: 25px;
    color: var(--ink);
    white-space: nowrap;
  }
  .social-square {
    width: 18px;
    height: 18px;
    background: var(--brand-blue);
  }
</style>
</head>
<body>
<main class="canvas">
  <section class="business-card">
    <div class="brand-lockup">
      <span class="brand-mark"></span>
      <span class="brand-name">Every Shelf Set Neatly</span>
    </div>

    <div class="contact-block">
      <p class="person-name">Lorna M. Pelham</p>
      <p class="person-title">Owner</p>
      <ul class="contact-list">
        <li class="contact-item">
          <svg class="contact-icon" viewBox="0 0 24 24" aria-hidden="true">
            <path fill="var(--brand-blue)" d="M6.6 10.8c1.4 2.8 3.8 5.1 6.6 6.6l2.2-2.2c.3-.3.7-.4 1-.2 1.1.4 2.3.6 3.6.6.6 0 1 .4 1 1V20c0 .6-.4 1-1 1C10.6 21 3 13.4 3 4c0-.6.4-1 1-1h3.5c.6 0 1 .4 1 1 0 1.3.2 2.5.6 3.6.1.3 0 .7-.2 1z"/>
          </svg>
          <span>418-552-7094</span>
        </li>
        <li class="contact-item">
          <svg class="contact-icon" viewBox="0 0 24 24" aria-hidden="true">
            <g fill="none" stroke="var(--brand-blue)" stroke-width="1.6">
              <circle cx="12" cy="12" r="9"/>
              <ellipse cx="12" cy="12" rx="4" ry="9"/>
              <line x1="3" y1="12" x2="21" y2="12"/>
              <line x1="4.5" y1="7.5" x2="19.5" y2="7.5"/>
              <line x1="4.5" y1="16.5" x2="19.5" y2="16.5"/>
            </g>
          </svg>
          <span>www.esnorganized-example.com</span>
        </li>
      </ul>
    </div>

    <p class="social-line">
      <span class="social-square"></span>
      <span>www.sociallink-example.com/everyshelfsetneatly</span>
    </p>
  </section>
</main>
</body>
</html>
```